Hunting club needs a new web design !

We need a new web design for our hunting club located in Poland, called "BORYNA". The club was founded in 1945. Colors that we would like to see in the project are the colors of the forest. The website should be built in such a way that all text elements can be changed to another language and can't be graphic.
"BORYNA" means - big, thick forest in which the game, small and big resides

Target Market(s)

hunters,

Industry/Entity Type

Hunting

Coding

Coded - Design and coding required

Number of Pages Required

5+ page

Font styles to use
Decorative

Colors

Designer to choose colors to be used in the design.

Requirements
Must have
• current date, calendar,
• must contain almost all materials from our current web page
• http://boryna-lasowiec.webnest.pl/
• new web address: borynalsw.pl
Nice to have
• current weather in three hunting regions that we allowed to hunt, or indicated by the visitor on the map placed on our web,
• actual phase of the moon, actual moon rising hour, actual moon set hour, actual sun rise hour, actual sun set hour, current weather in region (stalowa wola, poland)
• wood, forest, deers, boars,
Should not have
• mountain photos, modern look, white or bright backgrounds,

```html
<!DOCTYPE html>
<html lang="en">
<head>
<meta charset="utf-8">
<title>BORYNA Hunting Club</title>
<link rel="stylesheet" href="https://fonts.googleapis.com/css2?family=Open+Sans:wght@400;600;700;800&family=Roboto:ital,wght@0,300;0,400;0,500;0,700;1,400&display=swap">
<style>
:root{
  --green:#1f9a52;
  --green-bright:#2dbd74;
  --green-dark:#1b7a43;
  --brown:#7b4a22;
  --brown-dark:#6a3d19;
  --brown-mid:#8a5529;
  --brown-light:#9a6133;
  --text:#333;
  --muted:#666;
  --line:#d8d8d8;
  --footer:#262626;
  --white:#fff;
}
*{box-sizing:border-box;margin:0;padding:0}
html,body{width:1200px;height:2866px;overflow:hidden}
body{position:relative;background:var(--white);font-family:'Roboto',sans-serif;color:var(--text)}
.abs{position:absolute}
.top-bar{left:0;top:0;width:1200px;height:6px;background:var(--brown)}
/* header */
.brand{left:90px;top:30px;display:flex;align-items:center;gap:14px}
.brand-dot{width:52px;height:52px;border-radius:50%;background:var(--green-dark)}
.brand-name{font-family:'Roboto',sans-serif;font-weight:700;font-size:40px;color:var(--green-dark);letter-spacing:1px}
.today{left:657px;top:46px;font-size:17px;color:#555}
.today b{font-weight:400;color:var(--green)}
.btn-moon{left:881px;top:38px;width:122px;height:38px;border:1px solid var(--brown);border-radius:3px;color:var(--brown);font-size:15px;display:flex;align-items:center;justify-content:center}
.btn-lang{left:1013px;top:38px;width:97px;height:38px;background:var(--green);border-radius:3px;color:var(--white);font-size:15px;display:flex;align-items:center;justify-content:center;gap:6px}
.header-rule{left:90px;top:100px;width:1022px;height:1px;background:var(--line)}
.main-nav{left:105px;top:124px;width:994px;display:flex;justify-content:space-between;font-size:16px;color:#333}
/* hero */
.hero{left:0;top:168px;width:1200px;height:516px;background:radial-gradient(ellipse at 58% 18%,#f6d98a 0%,#d9a24c 18%,#8a5a2a 48%,#4a3019 80%,#2e1f12 100%)}
.hero-title{left:124px;top:375px;font-family:'Open Sans',sans-serif;font-weight:600;font-size:80px;letter-spacing:24px;color:var(--white)}
.hero-sub{left:124px;top:475px;font-family:'Open Sans',sans-serif;font-weight:600;font-size:26px;color:var(--white)}
.hero-arrows{left:140px;top:558px;display:flex;gap:6px}
.hero-arrows span{width:26px;height:26px;border-radius:50%;background:rgba(0,0,0,.35);display:flex;align-items:center;justify-content:center}
/* weather band */
.weather-band{left:0;top:684px;width:1200px;height:94px;background:var(--green-bright)}
.wb-title{left:90px;top:700px;font-size:27px;color:var(--white)}
.wb-text{left:90px;top:737px;font-size:15px;color:#eafff2}
.wb-box{left:814px;top:684px;width:298px;height:94px;background:#1e9a57;box-shadow:0 6px 14px rgba(0,0,0,.25)}
.wb-place{left:841px;top:704px;font-size:21px;color:var(--white)}
.wb-time{left:841px;top:731px;font-size:11px;color:#e2f5ea}
.wb-temp{left:930px;top:692px;font-size:52px;font-weight:300;color:var(--white)}
.wb-icon{left:1018px;top:700px}
/* about */
.about-img{left:128px;top:868px;width:382px;height:284px;background:linear-gradient(180deg,#d9dde0 0%,#eef0f1 45%,#9a8b76 75%,#cfd2d4 100%)}
.about-title{left:543px;top:888px;font-size:31px;color:#222}
.about-text{left:543px;top:936px;width:545px;font-size:13.5px;line-height:21.5px;color:var(--muted);text-align:justify}
.btn-more{left:543px;top:1105px;width:99px;height:30px;border-radius:15px;background:var(--brown);color:var(--white);font-size:12px;display:flex;align-items:center;justify-content:center}
/* stalowa */
.region{left:0;top:1232px;width:1200px;height:522px;background:linear-gradient(180deg,#eceeef 0%,#dfe3e4 55%,#b9c3c2 100%)}
.region-title{left:0;top:1295px;width:1200px;text-align:center;font-size:28px;color:#222}
.wcard{width:415px;height:286px;top:1386px;overflow:hidden;color:var(--white)}
.wcard-photo{position:absolute;inset:0}
.wcard-1{left:170px}
.wcard-1 .wcard-photo{background:linear-gradient(180deg,#4d5a6a 0%,#3f4648 45%,#4a3a2b 75%,#2a2420 100%)}
.wcard-2{left:613px}
.wcard-2 .wcard-photo{background:linear-gradient(180deg,#7f95a5 0%,#5f7470 35%,#4b7a33 65%,#3a5b28 100%)}
.wc{position:absolute}
.wc-day{font-size:22px}
.wc-date{font-size:10px}
.wc-place{font-size:12px}
.wc-temp{font-family:'Open Sans',sans-serif;font-weight:800;font-size:72px;line-height:1}
.wc-row{font-size:16px}
.forecast{position:absolute;left:0;bottom:8px;width:100%;height:60px}
.fc{position:absolute;top:0;width:90px;text-align:center;font-size:10px}
.fc svg{display:block;margin:3px auto 1px}
.fc-sep{position:absolute;top:4px;width:1px;height:50px;background:rgba(255,255,255,.4)}
.fc-arrow{position:absolute;top:20px}
/* news */
.sec-title{font-size:20px;color:#111}
.news-img{left:96px;width:185px;height:128px;border:4px solid #fff;box-shadow:0 1px 5px rgba(0,0,0,.3)}
.news-img.n1{top:1932px;background:linear-gradient(180deg,#cfd4c8 0%,#7e8f57 50%,#3e5a26 100%)}
.news-img.n2{top:2100px;background:linear-gradient(180deg,#e8e2b5 0%,#b6ad6d 45%,#6a7b37 100%)}
.news-t{left:302px;font-size:15px;color:#222}
.news-d{left:302px;font-size:12px;font-style:italic;color:#666}
.news-x{left:302px;width:260px;font-size:13px;line-height:20px;color:#666}
.news-m{left:302px;font-size:10px;color:var(--green)}
.news-rule{left:96px;top:2081px;width:475px;height:1px;background:#ccc}
/* calendar */
.cal{left:642px;top:1917px;width:472px;height:328px;box-shadow:0 3px 12px rgba(0,0,0,.25);background:#fff}
.cal-left{position:absolute;left:0;top:0;width:243px;height:328px;background:var(--brown)}
.cal-head{height:65px;background:var(--brown-dark);display:flex;align-items:center;justify-content:center;color:#fff;font-size:17px;position:relative}
.cal-head svg{position:absolute;left:18px;top:22px}
.cal-ev{height:61px;padding:10px 14px 0 34px;color:#fff;position:relative}
.cal-ev:nth-child(even){background:var(--brown-light)}
.cal-ev:nth-child(odd){background:var(--brown-mid)}
.cal-ev::before{content:"";position:absolute;left:20px;top:16px;width:6px;height:6px;border-radius:50%;background:#fff}
.cal-ev b{display:block;font-weight:400;font-size:12.5px}
.cal-ev span{font-size:9.5px;color:#f1e2d2}
.cal-right{position:absolute;left:243px;top:0;width:229px;height:328px}
.cal-month{position:absolute;left:0;top:26px;width:229px;text-align:center;font-size:18px;color:var(--green)}
.cal-grid{position:absolute;left:8px;top:76px;width:213px;display:grid;grid-template-columns:repeat(7,1fr);row-gap:9px;text-align:center;font-size:14px;color:#444}
.cal-grid .dw{font-size:13px;color:#222}
.cal-grid .off{color:#aaa}
.cal-grid .on{background:var(--green);color:#fff;border-radius:50%;width:24px;height:24px;line-height:24px;margin:-3px auto 0}
.cal-grid .faint{color:#ddd}
/* map */
.map{left:0;top:2360px;width:1200px;height:325px;background:linear-gradient(135deg,#d4d4d4 0%,#c7c7c7 50%,#d9d9d9 100%)}
.loc-card{left:245px;top:2452px;width:294px;height:115px;background:#fff;box-shadow:0 2px 10px rgba(0,0,0,.2)}
.loc-name{left:268px;top:2484px;font-size:21px;color:#333}
.loc-time{left:268px;top:2511px;font-size:11px;color:#777}
.loc-temp{left:363px;top:2472px;font-size:52px;font-weight:300;color:#2a8fc5}
/* footer */
.footer{left:0;top:2685px;width:1200px;height:181px;background:var(--footer)}
.foot-links{left:0;top:2734px;width:1200px;text-align:center;font-size:12px;color:#fff;letter-spacing:.5px}
.foot-links i{font-style:normal;margin:0 10px;color:#aaa}
.foot-social{left:0;top:2767px;width:1200px;display:flex;justify-content:center;gap:8px}
.foot-social span{width:28px;height:28px;border:1px solid #888;border-radius:50%}
.foot-copy{left:0;top:2809px;width:1200px;text-align:center;font-size:12px;color:#ddd}
</style>
</head>
<body>
<div class="abs top-bar"></div>

<header>
  <div class="abs brand"><span class="brand-dot"></span><span class="brand-name">BORYNA</span></div>
  <div class="abs today">Today's date : <b>18.08.2017</b></div>
  <div class="abs btn-moon">Moon Phases</div>
  <div class="abs btn-lang">English <svg width="9" height="6"><path d="M0 0h9L4.5 6z" fill="#fff"/></svg></div>
  <div class="abs header-rule"></div>
  <nav class="abs main-nav">
    <span>Wheel History</span><span>Board of the Wheel</span><span>Hunting Equipment</span><span>Hunting ethics</span><span>Hunting plan</span><span>Hunting calendar</span><span>Cynology</span><span>Gallery</span>
  </nav>
</header>

<section>
  <div class="abs hero" role="img" aria-label="Red deer stag standing in a misty meadow at golden sunrise"></div>
  <div class="abs hero-title">BORYNA</div>
  <div class="abs hero-sub">The club was founded in 1945</div>
  <div class="abs hero-arrows">
    <span><svg width="10" height="12"><path d="M7 1L2 6l5 5" stroke="#fff" stroke-width="2" fill="none"/></svg></span>
    <span><svg width="10" height="12"><path d="M3 1l5 5-5 5" stroke="#fff" stroke-width="2" fill="none"/></svg></span>
  </div>
</section>

<section>
  <div class="abs weather-band"></div>
  <div class="abs wb-title">Local Weather</div>
  <div class="abs wb-text">Neque porro quisquam est qui dolorem ipsum quia dolor sit amet, consectetur, adipisci velit...</div>
  <div class="abs wb-box"></div>
  <div class="abs wb-place">Poland</div>
  <div class="abs wb-time">2:00 pm</div>
  <div class="abs wb-temp">14°</div>
  <svg class="abs wb-icon" width="62" height="50" viewBox="0 0 62 50">
    <circle cx="22" cy="18" r="12" fill="#f5c33b"/>
    <path d="M14 36a9 9 0 0 1 4-17 12 12 0 0 1 23 3 8 8 0 0 1 2 14z" fill="#e9eef2"/>
    <path d="M24 42h20M28 47h14" stroke="#2a8fc5" stroke-width="3" stroke-linecap="round"/>
  </svg>
</section>

<section>
  <div class="abs about-img" role="img" aria-label="Deer among snow-covered trees in a winter forest"></div>
  <h2 class="abs about-title" style="font-weight:400">ABOUT US</h2>
  <p class="abs about-text">It is a long established fact that a reader will be distracted by the readable content of a page when looking at its layout. The point of using Lorem Ipsum is that it has a more-or-less normal distribution of letters, as opposed to using 'Content here, content here', making it look like readable English. Many desktop publishing packages and web page editors now use Lorem Ipsum as their default model text, and a search for 'lorem ipsum' will uncover many web sites still in their infancy. Various versions have evolved over the years, sometimes by accident, sometimes on purpose</p>
  <div class="abs btn-more">Read More »</div>
</section>

<section>
  <div class="abs region" role="img" aria-label="Misty pine forest backdrop"></div>
  <h2 class="abs region-title" style="font-weight:400">STALOWA WOLA, POLAND</h2>

  <div class="abs wcard wcard-1">
    <div class="wcard-photo" role="img" aria-label="Dusky landscape under a cloudy sky"></div>
    <div class="wc wc-day" style="left:69px;top:20px">Sunday</div>
    <div class="wc wc-date" style="left:69px;top:50px">June, 26th</div>
    <div class="wc wc-place" style="left:69px;top:64px">Poland</div>
    <div class="wc wc-temp" style="left:241px;top:12px">15°</div>
    <div class="wc wc-row" style="left:61px;top:112px">Actual phase of the moon</div><div class="wc wc-row" style="left:262px;top:112px">06:00 am</div>
    <div class="wc wc-row" style="left:61px;top:142px">Actual moon rising hour</div><div class="wc wc-row" style="left:262px;top:142px">03:33 am</div>
    <div class="wc wc-row" style="left:61px;top:171px">Actual moon set hour</div><div class="wc wc-row" style="left:262px;top:171px">4:24 pm</div>
    <div class="forecast">
      <svg class="fc-arrow" style="left:50px" width="10" height="14"><path d="M8 1L2 7l6 6" stroke="#fff" stroke-width="2" fill="none"/></svg>
      <div class="fc" style="left:65px">Monday<svg width="30" height="22"><path d="M6 14a5 5 0 0 1 2-9 8 8 0 0 1 15 2 4 4 0 0 1 1 7z" fill="none" stroke="#fff" stroke-width="1.5"/><path d="M10 18v3M15 18v3M20 18v3" stroke="#fff" stroke-width="1.5"/></svg>10</div>
      <div class="fc-sep" style="left:152px"></div>
      <div class="fc" style="left:153px">Tuesday<svg width="30" height="22"><path d="M6 18a5 5 0 0 1 2-9 8 8 0 0 1 15 2 4 4 0 0 1 1 7z" fill="none" stroke="#fff" stroke-width="1.5"/></svg>15</div>
      <div class="fc-sep" style="left:243px"></div>
      <div class="fc" style="left:244px">Wednesday<svg width="30" height="22"><circle cx="15" cy="11" r="5" fill="none" stroke="#fff" stroke-width="1.5"/><path d="M15 1v3M15 18v3M5 11h3M22 11h3M8 4l2 2M20 16l2 2M22 4l-2 2M10 16l-2 2" stroke="#fff" stroke-width="1.5"/></svg>23</div>
      <svg class="fc-arrow" style="left:350px" width="10" height="14"><path d="M2 1l6 6-6 6" stroke="#fff" stroke-width="2" fill="none"/></svg>
    </div>
  </div>

  <div class="abs wcard wcard-2">
    <div class="wcard-photo" role="img" aria-label="Green valley with a wooden cabin and path"></div>
    <div class="wc wc-day" style="left:71px;top:20px">Sunday</div>
    <div class="wc wc-date" style="left:71px;top:50px">June, 26th</div>
    <div class="wc wc-place" style="left:71px;top:64px">Poland</div>
    <div class="wc wc-temp" style="left:239px;top:12px">17°</div>
    <div class="wc wc-row" style="left:69px;top:119px">Actual sun rise hour</div><div class="wc wc-row" style="left:268px;top:119px">05:40 am</div>
    <div class="wc wc-row" style="left:69px;top:150px">Actual sun set hour</div><div class="wc wc-row" style="left:268px;top:150px">06:33 pm</div>
    <div class="forecast">
      <svg class="fc-arrow" style="left:50px" width="10" height="14"><path d="M8 1L2 7l6 6" stroke="#fff" stroke-width="2" fill="none"/></svg>
      <div class="fc" style="left:65px">Monday<svg width="30" height="22"><path d="M6 14a5 5 0 0 1 2-9 8 8 0 0 1 15 2 4 4 0 0 1 1 7z" fill="none" stroke="#fff" stroke-width="1.5"/><path d="M10 18v3M15 18v3M20 18v3" stroke="#fff" stroke-width="1.5"/></svg>10</div>
      <div class="fc-sep" style="left:152px"></div>
      <div class="fc" style="left:153px">Tuesday<svg width="30" height="22"><path d="M6 18a5 5 0 0 1 2-9 8 8 0 0 1 15 2 4 4 0 0 1 1 7z" fill="none" stroke="#fff" stroke-width="1.5"/></svg>15</div>
      <div class="fc-sep" style="left:243px"></div>
      <div class="fc" style="left:244px">Wednesday<svg width="30" height="22"><circle cx="15" cy="11" r="5" fill="none" stroke="#fff" stroke-width="1.5"/><path d="M15 1v3M15 18v3M5 11h3M22 11h3M8 4l2 2M20 16l2 2M22 4l-2 2M10 16l-2 2" stroke="#fff" stroke-width="1.5"/></svg>22</div>
      <svg class="fc-arrow" style="left:350px" width="10" height="14"><path d="M2 1l6 6-6 6" stroke="#fff" stroke-width="2" fill="none"/></svg>
    </div>
  </div>
</section>

<section>
  <h2 class="abs sec-title" style="left:96px;top:1872px;font-weight:400">LATEST NEWS</h2>
  <div class="abs news-img n1" role="img" aria-label="Young spruce trees in a misty field"></div>
  <div class="abs news-t" style="top:1943px">Nemo Enim Ipsam Voluptatem</div>
  <div class="abs news-d" style="top:1968px">July 20, 2017</div>
  <div class="abs news-x" style="top:1987px">Lorem ipsum dolor sit amet, consectetur adipiscing elit, sed do eiusmod tempor</div>
  <div class="abs news-m" style="top:2036px">Read More »</div>
  <div class="abs news-rule"></div>
  <div class="abs news-img n2" role="img" aria-label="Lone tree in a sunny meadow"></div>
  <div class="abs news-t" style="top:2111px">Nemo Enim Ipsam Voluptatem</div>
  <div class="abs news-d" style="top:2136px">July 20, 2017</div>
  <div class="abs news-x" style="top:2155px">Lorem ipsum dolor sit amet, consectetur adipiscing elit, sed do eiusmod tempor</div>
  <div class="abs news-m" style="top:2204px">Read More »</div>

  <h2 class="abs sec-title" style="left:642px;top:1872px;font-weight:400">HUNT CALENDAR</h2>
  <div class="abs cal">
    <div class="cal-left">
      <div class="cal-head"><svg width="12" height="20"><path d="M10 2L2 10l8 8" stroke="#fff" stroke-width="3" fill="none"/></svg>MONDAY</div>
      <div>
        <div class="cal-ev"><b>Neque porro quisquam est</b><span>Lorem ipsum has been the industry's</span></div>
        <div class="cal-ev"><b>Dolorem ipsum quia dolor</b><span>Lorem ipsum has been the industry's</span></div>
        <div class="cal-ev"><b>Neque porro quisquam est</b><span>Lorem ipsum has been the industry's</span></div>
        <div class="cal-ev"><b>Dolorem ipsum quia dolor</b><span>Lorem ipsum has been the industry's</span></div>
      </div>
    </div>
    <div class="cal-right">
      <div class="cal-month">JUNE 2017</div>
      <svg style="position:absolute;left:200px;top:26px" width="12" height="20"><path d="M2 2l8 8-8 8" stroke="#1f9a52" stroke-width="3" fill="none"/></svg>
      <div class="cal-grid">
        <span class="dw">S</span><span class="dw">M</span><span class="dw">T</span><span class="dw">W</span><span class="dw">R</span><span class="dw">F</span><span class="dw">S</span>
        <span class="off">28</span><span class="off">29</span><span class="off">30</span><span>1</span><span>2</span><span>3</span><span>4</span>
        <span>5</span><span>6</span><span>7</span><span>8</span><span>9</span><span>10</span><span>11</span>
        <span>12</span><span>13</span><span>14</span><span>15</span><span>16</span><span>17</span><span>18</span>
        <span>19</span><span>20</span><span>21</span><span>22</span><span><span class="on" style="display:block">23</span></span><span>24</span><span>25</span>
        <span>26</span><span>27</span><span>28</span><span>29</span><span>30</span><span>31</span><span class="faint">1</span>
      </div>
      <svg style="position:absolute;left:196px;top:298px" width="22" height="22"><circle cx="11" cy="11" r="9.5" fill="none" stroke="#1f9a52" stroke-width="1.5"/><path d="M11 6v10M6 11h10" stroke="#1f9a52" stroke-width="1.5"/></svg>
    </div>
  </div>
</section>

<section>
  <div class="abs map" role="img" aria-label="Street map of the hunting area"></div>
  <svg class="abs" style="left:754px;top:2404px" width="32" height="46"><path d="M16 45C16 45 2 26 2 16a14 14 0 0 1 28 0c0 10-14 29-14 29z" fill="#e25c5c"/><circle cx="16" cy="16" r="5" fill="#fff"/></svg>
  <svg class="abs" style="left:558px;top:2515px" width="46" height="64"><path d="M23 63C23 63 2 37 2 22a21 21 0 0 1 42 0c0 15-21 41-21 41z" fill="#e25c5c"/><circle cx="23" cy="22" r="7" fill="#fff"/></svg>
  <svg class="abs" style="left:1004px;top:2503px" width="32" height="46"><path d="M16 45C16 45 2 26 2 16a14 14 0 0 1 28 0c0 10-14 29-14 29z" fill="#e25c5c"/><circle cx="16" cy="16" r="5" fill="#fff"/></svg>
  <div class="abs loc-card"></div>
  <div class="abs loc-name">Location</div>
  <div class="abs loc-time">2:00 pm</div>
  <div class="abs loc-temp">12°</div>
  <svg class="abs" style="left:458px;top:2480px" width="62" height="50" viewBox="0 0 62 50">
    <circle cx="22" cy="18" r="12" fill="#f5c33b"/>
    <path d="M14 36a9 9 0 0 1 4-17 12 12 0 0 1 23 3 8 8 0 0 1 2 14z" fill="#dfe6ec"/>
    <path d="M24 42h20M28 47h14" stroke="#2a8fc5" stroke-width="3" stroke-linecap="round"/>
  </svg>
</section>

<footer>
  <div class="abs footer"></div>
  <div class="abs foot-links">ABOUT<i>|</i>PRIVACY<i>|</i>TERMS<i>|</i>LEGAL<i>|</i>CONTACT</div>
  <div class="abs foot-social"><span></span><span></span><span></span><span></span><span></span><span></span></div>
  <div class="abs foot-copy">Copyright © 2017 All Rights Reserved</div>
</footer>
</body>
</html>
```